I need a design that promotes "A peak path hub for runners". services include assessment, massage, physiotherapy, pilates, suspension training, kinesiotaping in any combination.
I would like to bring the design into my website, flyers etc

Target Market(s)

athletes from beginner to elite - any age, male and female

Industry/Entity Type

Shop

Contact Information for Business Card

Peak-Path Hub for Runners
17 Corla Lane, Westmere, Tauranga
021 874 3061
tess.harlow@mailbrook.example

Logo Text

Logo styles of interest
Abstract Logo
Requirements
Nice to have
• Blue colour theme

```html
<!DOCTYPE html>
<html lang="en">
<head>
<meta charset="utf-8">
<title>Peak-Path Hub for Runners – Business Card</title>
<link rel="stylesheet" href="https://fonts.googleapis.com/css2?family=Oswald:wght@700&family=Open+Sans:wght@400&display=swap">
<style>
  :root {
    --navy: #050b5c;
    --sky: #3fbcf5;
    --white: #ffffff;
    --page: #e9ebef;
    --shadow: rgba(5, 11, 92, 0.25);
  }
  * { box-sizing: border-box; margin: 0; padding: 0; }
  html, body {
    width: 1200px;
    height: 1000px;
    overflow: hidden;
    background: var(--page);
  }
  .sheet {
    position: relative;
    width: 1200px;
    height: 1000px;
  }
  .card {
    position: absolute;
    left: 220px;
    width: 760px;
    height: 420px;
    border-radius: 30px;
    background: var(--navy);
    overflow: hidden;
    box-shadow: 0 10px 24px var(--shadow);
  }
  .card--front { top: 60px; }
  .card--back { top: 520px; }

  /* Front */
  .top-rule {
    position: absolute;
    left: 0; right: 0;
    top: 44px;
    height: 7px;
    background: var(--sky);
  }
  .brand {
    position: absolute;
    left: 70px;
    top: 100px;
    display: flex;
    align-items: center;
    gap: 14px;
  }
  .brand__dot {
    width: 58px;
    height: 58px;
    border-radius: 50%;
    background: var(--sky);
    flex: none;
  }
  .brand__name {
    font-family: "Oswald", sans-serif;
    font-weight: 700;
    font-size: 44px;
    letter-spacing: 0.2px;
    color: var(--sky);
    text-transform: uppercase;
    line-height: 1;
    white-space: nowrap;
  }
  .contact {
    position: absolute;
    left: 230px;
    top: 170px;
    width: 300px;
    font-family: "Open Sans", sans-serif;
    font-style: normal;
    color: var(--sky);
    text-align: center;
    line-height: 1.3;
  }
  .contact__name { font-size: 25px; }
  .contact__address { font-size: 21px; }
  .contact-band {
    position: absolute;
    left: 0; right: 0;
    top: 292px;
    height: 90px;
    background: var(--sky);
    font-family: "Open Sans", sans-serif;
    font-size: 22px;
    line-height: 1;
    color: var(--white);
  }
  .contact-band__email {
    position: absolute;
    right: 40px;
    top: 14px;
  }
  .contact-band__phone {
    position: absolute;
    left: 70px;
    bottom: 14px;
  }

  /* Back */
  .hero-disc {
    position: absolute;
    left: -150px;
    top: -110px;
    width: 540px;
    height: 540px;
    border-radius: 50%;
    background: var(--sky);
  }
  .services {
    position: absolute;
    left: 450px;
    top: 80px;
    display: flex;
    gap: 16px;
    font-family: "Open Sans", sans-serif;
  }
  .services__label {
    display: flex;
    flex-direction: column;
    align-items: center;
    color: var(--white);
    font-size: 25px;
    line-height: 29px;
  }
  .services__rule {
    width: 2px;
    background: var(--sky);
  }
  .services__list {
    list-style: none;
    color: var(--sky);
    font-size: 23px;
    line-height: 36px;
    padding-top: 6px;
  }
</style>
</head>
<body>
<main class="sheet">

  <section class="card card--front" aria-label="Business card front">
    <div class="top-rule"></div>
    <div class="brand">
      <span class="brand__dot"></span>
      <h1 class="brand__name">Peak-Path Hub for Runners</h1>
    </div>
    <address class="contact">
      <p class="contact__name">Tess Harlow</p>
      <p class="contact__address">17 Corla Lane,<br>Westmere,<br>Tauranga</p>
    </address>
    <div class="contact-band">
      <span class="contact-band__email">tess.harlow@mailbrook.example</span>
      <span class="contact-band__phone">Phone 021 874 3061</span>
    </div>
  </section>

  <section class="card card--back" aria-label="Business card back">
    <div class="hero-disc" role="img" aria-label="White silhouette of a sprinting runner on a sky-blue circle"></div>
    <div class="services">
      <div class="services__label" aria-label="services">
        <span>s</span><span>e</span><span>r</span><span>v</span><span>i</span><span>c</span><span>e</span><span>s</span>
      </div>
      <div class="services__rule"></div>
      <ul class="services__list">
        <li>Assessment</li>
        <li>Massage</li>
        <li>Physiotherapy</li>
        <li>Pilates</li>
        <li>Suspension training</li>
        <li>Kinesiotaping</li>
        <li>in any combination.</li>
      </ul>
    </div>
  </section>

</main>
</body>
</html>
```